Local Flower Farm Needs Business Card Design

I need business cards designed for a flower farm based in Eudora, Kansas.
Business Info:
We are a local cut flower farm located in Eudora, Kansas, founded by Corinne Haldwick. What started as a passion for agriculture and search for more joy in daily life has blossomed into a small business dedicated to providing the community with beautiful, fresh, and sustainable flowers. We specialize in local, seasonal blooms, ensuring that every petal reflects the care and dedication we pour into our craft. Our mission is to deliver the highest quality flowers directly to our customers through local farmers markets and to florists who share our commitment to sustainability. Join us in celebrating the beauty of nature, one bloom at a time!
Contact Details:
Corinne Haldwick
Owner
Phone 913-555-0147
Facebook: Rosalind Thorpe Gardens
Instagram: @RosalindThorpeGardens
Website: RosalindThorpeGardens.example
Target Market(s)
Wholesale to Florists and Direct to Consumer via Farmers Market
Industry/Entity Type
Florist, Farm
Contact Information for Business Card
Name, Contact Info, Logo
Look and feel
Each slider illustrates characteristics of the customer's brand and the style your logo design should communicate.

```html
<!DOCTYPE html>
<html lang="en">
<head>
<meta charset="utf-8">
<title>Rosalind Thorpe Gardens – Business Card</title>
<link href="https://fonts.googleapis.com/css2?family=Libre+Caslon+Text&family=Quicksand:wght@500&display=swap" rel="stylesheet">
<style>
  :root {
    --stage: #1c1c1d;
    --teal: #0d2a30;
    --paper: #ffffff;
    --ink: #0d2a30;
    --bloom-light: #3c5a60;
  }
  * { margin: 0; padding: 0; box-sizing: border-box; }
  html, body { width: 1200px; height: 1015px; overflow: hidden; background: var(--stage); }
  .stage {
    width: 1200px; height: 1015px;
    display: flex; flex-direction: column; align-items: center; justify-content: center; gap: 56px;
  }
  .card {
    position: relative; width: 640px; height: 366px; overflow: hidden;
    box-shadow: 0 18px 40px rgba(0,0,0,.55);
  }
  /* front */
  .card--front { background: var(--teal); }
  .brand-seal {
    position: absolute; left: 170px; top: 58px; width: 230px; height: 230px;
    border: 1.5px solid rgba(255,255,255,.85); border-radius: 50%;
    display: flex; align-items: center; justify-content: center; text-align: center;
  }
  .brand-name {
    font-family: "Libre Caslon Text", serif; color: var(--paper);
    font-size: 23px; line-height: 1.3; letter-spacing: 2px; text-transform: uppercase;
  }
  /* back */
  .card--back { background: var(--teal); }
  .floral-art {
    position: absolute; left: 24px; top: 96px; width: 250px; height: 270px;
    background: radial-gradient(ellipse at 55% 45%, var(--bloom-light) 0%, rgba(60,90,96,.35) 50%, rgba(13,42,48,0) 78%);
  }
  .back-panel {
    position: absolute; left: 280px; top: 0; right: 0; bottom: 0;
    background: var(--paper); border-top-left-radius: 52px;
  }
  .identity { position: absolute; right: 56px; top: 42px; text-align: right; color: var(--ink); }
  .identity__name {
    font-family: "Libre Caslon Text", serif; font-weight: 400; font-size: 20px; letter-spacing: 1.5px; text-transform: uppercase;
  }
  .identity__role { font-family: "Quicksand", sans-serif; font-weight: 500; font-size: 14px; margin-top: 2px; }
  .identity__rule { display: block; margin: 14px 0 0 auto; width: 60px; }
  .contacts {
    position: absolute; right: 26px; bottom: 52px; list-style: none;
    font-family: "Quicksand", sans-serif; font-weight: 500; font-size: 16px; color: var(--ink);
  }
  .contacts li { display: flex; align-items: center; justify-content: flex-end; gap: 9px; height: 29px; white-space: nowrap; }
  .contact-icon { width: 22px; height: 22px; flex: none; }
</style>
</head>
<body>
<main class="stage">
  <section class="card card--front">
    <div class="brand-seal">
      <span class="brand-name">Rosalind Thorpe<br>Gardens</span>
    </div>
  </section>

  <section class="card card--back">
    <div class="floral-art" role="img" aria-label="Line-drawn bouquet of white wildflowers and stems"></div>
    <div class="back-panel"></div>

    <div class="identity">
      <h1 class="identity__name">Corinne Haldwick</h1>
      <p class="identity__role">Owner</p>
      <svg class="identity__rule" viewBox="0 0 60 6" aria-hidden="true">
        <line x1="3" y1="3" x2="57" y2="3" stroke="#0d2a30" stroke-width="1.2"/>
        <circle cx="3" cy="3" r="2.2" fill="#0d2a30"/><circle cx="57" cy="3" r="2.2" fill="#0d2a30"/>
      </svg>
    </div>

    <ul class="contacts">
      <li>913-555-0147
        <svg class="contact-icon" viewBox="0 0 24 24" aria-hidden="true">
          <circle cx="12" cy="12" r="11" fill="none" stroke="#0d2a30" stroke-width="1.2"/>
          <path d="M8.5 7c.6-.5 1.3-.4 1.6.2l.9 1.7c.3.5.1 1-.3 1.3l-.6.5c.6 1.3 1.6 2.3 2.9 2.9l.5-.6c.3-.4.9-.6 1.3-.3l1.7.9c.6.3.7 1 .2 1.6-.9 1-2.2 1.2-3.6.5-2.1-1-3.7-2.6-4.7-4.7-.7-1.4-.5-2.7.1-4z" fill="#0d2a30"/>
        </svg>
      </li>
      <li>Rosalind Thorpe Gardens
        <svg class="contact-icon" viewBox="0 0 24 24" aria-hidden="true"><circle cx="12" cy="12" r="11" fill="none" stroke="#0d2a30" stroke-width="1.2"/></svg>
      </li>
      <li>@RosalindThorpeGardens
        <svg class="contact-icon" viewBox="0 0 24 24" aria-hidden="true"><circle cx="12" cy="12" r="11" fill="none" stroke="#0d2a30" stroke-width="1.2"/></svg>
      </li>
      <li>RosalindThorpeGardens.example
        <svg class="contact-icon" viewBox="0 0 24 24" aria-hidden="true">
          <circle cx="12" cy="12" r="11" fill="none" stroke="#0d2a30" stroke-width="1.2"/>
          <circle cx="12" cy="12" r="6.5" fill="none" stroke="#0d2a30" stroke-width="1.2"/>
          <ellipse cx="12" cy="12" rx="2.8" ry="6.5" fill="none" stroke="#0d2a30" stroke-width="1"/>
          <line x1="5.5" y1="12" x2="18.5" y2="12" stroke="#0d2a30" stroke-width="1"/>
        </svg>
      </li>
    </ul>
  </section>
</main>
</body>
</html>
```